Veldmark Supplies Business Card

Professional business card that stand out to our potential customers. Front and back with clean modern design

Industry/Entity Type

Oil and gas

Contact Information for Business Card

Name, address, website , office phone and cell number

Requirements
Must have
• Editable files for each employee

```html
<!DOCTYPE html>
<html lang="en">
<head>
<meta charset="utf-8">
<title>Veldmark Supplies Business Card</title>
<link href="https://fonts.googleapis.com/css2?family=Poppins:wght@300;400;700&display=swap" rel="stylesheet">
<style>
  :root {
    --red: #f50000;
    --blue: #06b0d0;
    --black: #000000;
    --white: #ffffff;
    --ink: #111111;
    --shadow: rgba(0, 0, 0, 0.28);
  }
  * { margin: 0; padding: 0; box-sizing: border-box; }
  html, body {
    width: 1100px;
    height: 1200px;
    overflow: hidden;
    background: var(--white);
    font-family: "Poppins", sans-serif;
  }
  .canvas { position: relative; width: 1100px; height: 1200px; }

  .card {
    position: absolute;
    left: 116px;
    width: 871px;
    height: 470px;
    background: var(--white);
    box-shadow: 10px 14px 26px var(--shadow);
  }
  .card--front { top: 62px; }
  .card--back { top: 662px; }

  .front-panel {
    position: absolute;
    left: 23px; top: 13px; right: 23px; bottom: 13px;
    background: var(--black);
  }

  .brand {
    position: absolute;
    display: flex;
    align-items: center;
    gap: 14px;
    font-weight: 700;
    text-transform: uppercase;
    white-space: nowrap;
    transform: translateX(-50%);
  }
  .brand__square { display: block; background: var(--red); }
  .brand--front { left: 50%; top: 195px; font-size: 40px; color: var(--white); letter-spacing: 1px; }
  .brand--front .brand__square { width: 38px; height: 38px; }
  .brand--back { left: 257px; top: 200px; font-size: 23px; color: var(--red); letter-spacing: 0.5px; }
  .brand--back .brand__square { width: 22px; height: 22px; }

  .divider {
    position: absolute;
    left: 468px; top: 123px;
    width: 2px; height: 222px;
    background: var(--blue);
  }

  .person-name {
    position: absolute;
    left: 513px; top: 112px;
    font-size: 33px;
    font-weight: 300;
    color: var(--ink);
    letter-spacing: 2px;
  }

  .contact-list { position: absolute; left: 484px; top: 160px; list-style: none; }
  .contact-item {
    display: flex;
    align-items: center;
    height: 27.5px;
    font-size: 19px;
    font-weight: 300;
    color: var(--ink);
    letter-spacing: 2px;
  }
  .contact-item--web { margin-top: 4px; }
  .contact-icon { width: 18px; height: 18px; margin-right: 11px; fill: var(--blue); flex: none; }

  .footer-band { position: absolute; left: 23px; bottom: 13px; width: 825px; height: 29px; }
</style>
</head>
<body>
<div class="canvas">

  <section class="card card--front">
    <div class="front-panel">
      <div class="brand brand--front"><span class="brand__square"></span>Veldmark Supplies</div>
    </div>
  </section>

  <section class="card card--back">
    <div class="brand brand--back"><span class="brand__square"></span>Veldmark Supplies</div>

    <div class="divider"></div>

    <h1 class="person-name">NAME</h1>

    <ul class="contact-list">
      <li class="contact-item">
        <svg class="contact-icon" viewBox="0 0 24 24" aria-hidden="true"><path d="M6.6 10.8a15 15 0 0 0 6.6 6.6l2.2-2.2a1 1 0 0 1 1-.25 11.4 11.4 0 0 0 3.6.57 1 1 0 0 1 1 1V20a1 1 0 0 1-1 1A17 17 0 0 1 3 4a1 1 0 0 1 1-1h3.5a1 1 0 0 1 1 1c0 1.25.2 2.45.57 3.57a1 1 0 0 1-.25 1z"/></svg>
        0123456789
      </li>
      <li class="contact-item">
        <svg class="contact-icon" viewBox="0 0 24 24" aria-hidden="true"><path d="M2 9c0-3 4.5-5 10-5s10 2 10 5v1.5h-5V8.5H7v2H2z"/><path d="M6 12l2-2h8l2 2v8H6z"/></svg>
        0123456789
      </li>
      <li class="contact-item">
        <svg class="contact-icon" viewBox="0 0 24 24" aria-hidden="true"><path d="M12 2a7 7 0 0 0-7 7c0 5.2 7 13 7 13s7-7.8 7-13a7 7 0 0 0-7-7zm0 9.5A2.5 2.5 0 1 1 12 6.5a2.5 2.5 0 0 1 0 5z"/></svg>
        addresscityname000
      </li>
      <li class="contact-item">
        <svg class="contact-icon" viewBox="0 0 24 24" aria-hidden="true"><path d="M2 5h20v14H2zm2 2v.4l8 5.6 8-5.6V7zm0 2.8V17h16V9.8l-8 5.6z"/></svg>
        youremail@mailbox.com
      </li>
      <li class="contact-item contact-item--web">
        <svg class="contact-icon" viewBox="0 0 24 24" aria-hidden="true"><path d="M12 2a10 10 0 1 0 0 20 10 10 0 0 0 0-20zm6.9 6h-3a15 15 0 0 0-1.3-3.9A8 8 0 0 1 18.9 8zM12 4c.9 1.2 1.6 2.6 2 4h-4c.4-1.4 1.1-2.8 2-4zM4.3 14a8 8 0 0 1 0-4h3.3a16 16 0 0 0 0 4zm.8 2h3a15 15 0 0 0 1.3 3.9A8 8 0 0 1 5.1 16zm3-8h-3a8 8 0 0 1 4.3-3.9A15 15 0 0 0 8.1 8zM12 20c-.9-1.2-1.6-2.6-2-4h4c-.4 1.4-1.1 2.8-2 4zm2.3-6H9.7a14 14 0 0 1 0-4h4.6a14 14 0 0 1 0 4zm.3 5.9a15 15 0 0 0 1.3-3.9h3a8 8 0 0 1-4.3 3.9zM16.4 14a16 16 0 0 0 0-4h3.3a8 8 0 0 1 0 4z"/></svg>
        www.yourwebsite.com
      </li>
    </ul>

    <svg class="footer-band" viewBox="0 0 825 29" preserveAspectRatio="none" aria-hidden="true">
      <polygon points="0,0 417,0 408,29 0,29" fill="var(--red)"/>
      <polygon points="422,0 825,0 825,29 413,29" fill="var(--blue)"/>
    </svg>
  </section>

</div>
</body>
</html>
```